Website Banner Ad Design - 4x 200x200px panels that will rotate

I'm looking for four (4) 200x200px "panels" that will rotate on a website. Each one should have a unique description or key words on it, that makes it attractive to customers. It is important that each individual one kinda fits to our logo design to give it a "uniform" design.
The first panel should just be our logo and a slogan that says "AFFORDABLE. ACCELERATED. EFFECTIVE." This panel should also list our website "www.rotavex.com"
The second panel should have the following key text:
- Accelerated Training Courses
- Private Pilot in 4-weeks
- Career Programs from PPL to CFII
- Pay-as-you-go
The third panel should have the following key text:
- Advanced Training
- Firefighting (KRGA) & Forestry Tactics Training
- QT 740 & Varn 318K Turbine Transition Training
- External-Load (VR) Courses
THE fourth panel should list our website address "www.rotavex.com" and phone number: (555) 218-4073.
I give free hand with the design. Any idea is welcome. See attached some photos and logo that can be used. If you visit http://www.vantorwing.com/PILOTLESSONS/tabid/583/Default.aspx you can see other 200x200 panels to get an idea of what we're looking for. Our look has to be professional and stick out from the rest of our competitors. By questions, just PM me.

```html
<!DOCTYPE html>
<html lang="en">
<head>
<meta charset="utf-8">
<title>Rotavex Rotating Panels</title>
<link rel="stylesheet" href="https://fonts.googleapis.com/css2?family=Oswald:wght@400;500;600&family=PT+Serif&display=swap">
<style>
  :root {
    --page: #ffffff;
    --frame: #cfcfcf;
    --brand: #1f6fc0;
    --ink: #2b2b2b;
    --ink-soft: #444444;
    --veil: rgba(240, 240, 240, 0.86);
    --band: rgba(255, 255, 255, 0.82);
  }
  * { box-sizing: border-box; margin: 0; padding: 0; }
  html, body {
    width: 1200px; height: 1177px; overflow: hidden;
    background: var(--page);
  }
  .board { position: relative; width: 1200px; height: 1177px; }
  .panel {
    position: absolute; width: 522px; height: 517px;
    overflow: hidden; border: 2px solid var(--frame);
  }
  .panel--slogan { left: 57px; top: 51px; }
  .panel--courses { left: 631px; top: 51px; }
  .panel--advanced { left: 57px; top: 614px; }
  .panel--contact { left: 631px; top: 614px; }

  .photo { position: absolute; inset: 0; }
  .photo--helicopter-field {
    background: linear-gradient(180deg, #2f7fd0 0%, #8fc0ea 38%, #dfe9f0 52%, #6f9a44 70%, #3d6a2a 100%);
  }
  .photo--pilot-cabin {
    background: linear-gradient(160deg, #7d8d5c 0%, #55643a 40%, #2c3324 75%, #1a1d16 100%);
  }
  .photo--cockpit {
    background: linear-gradient(170deg, #3b4a57 0%, #1c252d 45%, #2b3036 75%, #111519 100%);
  }
  .photo--pilot-sky {
    background: linear-gradient(135deg, #5e7f98 0%, #9fb6c6 35%, #dfe6ea 60%, #7f9a6a 85%, #4a6a3a 100%);
  }

  .slogan { position: absolute; left: 16px; top: 26px; list-style: none; }
  .slogan li {
    display: block; width: max-content; margin-bottom: 36px;
    padding: 2px 14px 4px 14px;
    background: var(--veil);
    font-family: "Oswald", sans-serif; font-weight: 500;
    font-size: 42px; line-height: 52px; letter-spacing: 2px;
    color: var(--ink);
  }

  .key-list {
    position: absolute; list-style: none;
    background: var(--veil); color: var(--ink);
  }
  .key-list li { white-space: nowrap; }
  .key-list--courses {
    left: 18px; top: 39px; width: 488px; height: 300px;
    padding: 18px 0 0 14px;
    font-family: "PT Serif", serif; font-size: 25px; line-height: 66px;
  }
  .key-list--advanced {
    left: 16px; top: 57px; width: 490px; height: 333px;
    padding: 24px 0 0 14px;
    font-family: "Oswald", sans-serif; font-size: 25px; line-height: 62px;
    color: var(--ink-soft);
  }

  .phone {
    position: absolute; left: 151px; top: 285px; width: 345px; height: 73px;
    background: var(--veil);
    font-family: "Oswald", sans-serif; font-size: 34px; line-height: 73px;
    text-align: center; color: var(--ink);
  }

  .brand-band {
    position: absolute; left: 0; right: 0; bottom: 0; height: 98px;
    background: var(--band);
    display: flex; align-items: center; justify-content: space-between;
    padding: 0 22px 0 16px;
  }
  .site-url {
    font-family: "PT Serif", serif; font-size: 30px; color: var(--ink);
  }
  .brand-name {
    font-family: "Oswald", sans-serif; font-weight: 600;
    font-size: 54px; line-height: 1; color: var(--brand);
    text-transform: lowercase;
  }
</style>
</head>
<body>
<main class="board">

  <section class="panel panel--slogan">
    <div class="photo photo--helicopter-field" role="img" aria-label="Training helicopter on a grass field under a blue sky"></div>
    <ul class="slogan">
      <li>AFFORDABLE</li>
      <li>ACCELERATED</li>
      <li>EFFECTIVE</li>
    </ul>
    <footer class="brand-band">
      <span class="site-url">www.rotavex.com</span>
      <span class="brand-name">rotavex</span>
    </footer>
  </section>

  <section class="panel panel--courses">
    <div class="photo photo--pilot-cabin" role="img" aria-label="Pilot seated in a helicopter cabin"></div>
    <ul class="key-list key-list--courses">
      <li>-&gt; Accelerated Training Courses</li>
      <li>-&gt; Private Pilot in 4-weeks</li>
      <li>-&gt; Career Programs from PPL to CFII</li>
      <li>-&gt; Pay-as-you-go</li>
    </ul>
    <footer class="brand-band">
      <span class="site-url">www.rotavex.com</span>
      <span class="brand-name">rotavex</span>
    </footer>
  </section>

  <section class="panel panel--advanced">
    <div class="photo photo--cockpit" role="img" aria-label="Helicopter cockpit instrument panel"></div>
    <ul class="key-list key-list--advanced">
      <li>- Advanced Training</li>
      <li>- Firefighting (KRGA) &amp; Forestry Tactics Training</li>
      <li>- QT 740 &amp; Varn 318K Turbine Transition Training</li>
      <li>- External-Load (VR) Courses</li>
    </ul>
    <footer class="brand-band">
      <span class="site-url">www.rotavex.com</span>
      <span class="brand-name">rotavex</span>
    </footer>
  </section>

  <section class="panel panel--contact">
    <div class="photo photo--pilot-sky" role="img" aria-label="Helmeted pilot in an open helicopter door against a cloudy sky"></div>
    <p class="phone">Call : (555) 218-4073</p>
    <footer class="brand-band">
      <span class="site-url">www.rotavex.com</span>
      <span class="brand-name">rotavex</span>
    </footer>
  </section>

</main>
</body>
</html>
```